Elegant and modern Wedding Photography brochure

My existing brochure (attached) needs a major facelift. This is one of the main selling tools - it gets emailed to my clients when they make an equiry on what packages i offer and it is printed out and walked through at our first meeting. This brochure is as critical as my website - it needs to sing!

I'm looking for an eye-catching design that says:
Elegant
Modern
Clean
Crisp
Not cutesy or lovey-dovey thanks - we are more sophisticated and professional than that.

Update images to some of the latest weddings I've shot also. Let me know files and resolution you need. I've enabled right-click to download images on my site for a limited time. Please note that I retain copyright and will pursue any breeches.

Http://www.sarahkelbrin.com/Melbourne-wedding-photography
Updates

Thanks for all of your designs! Will take a few days to decide.

Target Market(s)

Australian Women aged 24-44

Industry/Entity Type

Wedding

Font styles to use
Other font styles liked:
• Century Gothic

Requirements
Must have
• Easy to print - does not have to be 6 A4 pages like the existing brochure
Nice to have
• Some full page images - The photos are supposed to be the hero here :-)
Should not have
• Not cutesy or lovey-dovey thanks - we are more sophisticated and professional than that.

No black backgrounds, I prefer a white thanks

No images in organic shaped boxes (like the rectangles in the logo - no thanks).
Keep the lines straight and sharp

```html
<!DOCTYPE html>
<html lang="en">
<head>
<meta charset="utf-8">
<title>Claire's approach – Wedding Photography</title>
<link href="https://fonts.googleapis.com/css2?family=Didact+Gothic&family=Poppins:wght@600&display=swap" rel="stylesheet">
<style>
  :root {
    --plum: #8b2a8c;
    --frame-grey: #96969a;
    --ink: #1d1d1b;
    --paper: #ffffff;
  }
  * { margin: 0; padding: 0; box-sizing: border-box; }
  html, body { width: 853px; height: 1200px; overflow: hidden; background: var(--paper); }
  .page {
    position: relative;
    width: 853px;
    height: 1200px;
    overflow: hidden;
    background: var(--paper);
    font-family: "Didact Gothic", "Century Gothic", sans-serif;
    color: var(--ink);
  }

  /* photo frames: straight, sharp-cornered */
  .photo {
    position: absolute;
    border: 8px solid var(--frame-grey);
    background: var(--paper);
  }
  .photo--plum { border-color: var(--plum); }
  .photo__fill { width: 100%; height: 100%; }
  .photo--couple   { left: 80px;  top: 144px; width: 240px; height: 180px; }
  .photo--bouquet  { left: 284px; top: 44px;  width: 240px; height: 188px; }
  .photo--party    { left: 440px; top: 164px; width: 226px; height: 192px; }
  .photo--portrait { left: 624px; top: 104px; width: 180px; height: 144px; }
  .photo--couple   .photo__fill { background: linear-gradient(135deg, #d9ccb0, #8f8a63 55%, #e8dccb); }
  .photo--bouquet  .photo__fill { background: linear-gradient(180deg, #ece6e3, #e3c4c6 45%, #d8d3cf); }
  .photo--party    .photo__fill { background: linear-gradient(180deg, #a99a6a, #6f6a48 45%, #eeeeee 70%, #2a2f45); }
  .photo--portrait .photo__fill { background: linear-gradient(135deg, #6f6548, #d9b6a4 50%, #efeae6); }

  /* heading */
  .title {
    position: absolute; left: 58px; top: 398px;
    font-family: "Poppins", "Century Gothic", sans-serif;
    font-weight: 600; font-size: 40px; line-height: 50px;
    color: var(--plum); letter-spacing: -0.3px;
  }
  .subtitle {
    position: absolute; left: 58px; top: 444px;
    font-size: 18.5px; line-height: 22px;
  }

  /* columns */
  .column { position: absolute; width: 345px; }
  .column--left  { left: 58px;  top: 488px; }
  .column--right { left: 451px; top: 508px; }
  .section__heading {
    font-family: "Poppins", "Century Gothic", sans-serif;
    font-weight: 600; font-size: 14.5px; line-height: 20px;
    color: var(--plum);
  }
  .section__heading--spaced { margin-bottom: 22px; }
  .section__text {
    font-size: 17.4px; line-height: 20.7px; letter-spacing: 0.15px;
    hyphens: auto; -webkit-hyphens: auto;
  }
  .section__text + .section__text { margin-top: 20.7px; }
  .section + .section { margin-top: 20.7px; }

  /* testimonial */
  .testimonial {
    position: absolute; left: 506px; top: 950px;
    width: 214px; height: 176px;
    border: 8px solid var(--plum);
    display: flex; flex-direction: column; align-items: center; justify-content: center;
    text-align: center; padding: 8px 14px;
  }
  .testimonial__quote { font-size: 14.5px; line-height: 18px; }
  .testimonial__cite { font-size: 8.5px; margin-top: 2px; font-style: normal; }

  /* studio name */
  .studio-name {
    position: absolute; left: 80px; top: 1104px;
    font-size: 14px; color: var(--plum);
  }
</style>
</head>
<body>
<main class="page">
  <div class="photo photo--couple"><div class="photo__fill" role="img" aria-label="Bride and groom smiling at each other outdoors"></div></div>
  <div class="photo photo--bouquet photo--plum"><div class="photo__fill" role="img" aria-label="Bouquet of pale pink roses in a glass vase"></div></div>
  <div class="photo photo--party"><div class="photo__fill" role="img" aria-label="Bride laughing with bridesmaids in navy dresses under willow trees"></div></div>
  <div class="photo photo--portrait photo--plum"><div class="photo__fill" role="img" aria-label="Close portrait of a smiling bride wearing a veil"></div></div>

  <h1 class="title">Claire’s approach…</h1>
  <p class="subtitle">Enjoy your special day</p>

  <div class="column column--left">
    <section class="section">
      <h2 class="section__heading section__heading--spaced">Style &amp; Approach</h2>
      <p class="section__text">Claire can observe and capture your wedding day in the background, quickly and quietly taking photojournalistic pictures rather than directing it if you prefer. Or she can confidently play the role of Art Director and instruct beautiful poses. Either way, what is most important is that her clients are relaxed and having a really great time on their wedding day!</p>
    </section>
    <section class="section">
      <h2 class="section__heading">Formal Photography</h2>
      <p class="section__text">Many of Claire’s clients book her because of the easy-going approach she has. They can get on with having a great time on their day without worrying about formal photography. However, there are occasions when clients do want formal family pictures, and Claire is more than happy to accommodate their requests.</p>
      <p class="section__text">In order to keep the disruption on the day to a minimum, we recommend that Claire photographs no more than 6 groups, and a select number of the special couple.</p>
    </section>
  </div>

  <div class="column column--right">
    <section class="section">
      <h2 class="section__heading section__heading--spaced">Image Presentation</h2>
      <p class="section__text">The most professional way of presenting clients with their photographs is in an elegantly designed photo book. Claire’s clients only pay one fixed price for the photography, regardless of how many images taken. There are no hard sell procedures to go through, and the completed book is prepared within 2-6 weeks after the wedding day.</p>
    </section>
    <section class="section">
      <h2 class="section__heading section__heading--spaced">Time of Year</h2>
      <p class="section__text">Signature pictures can be taken on overcast days or winter months. Don’t worry if the sky is not perfectly blue. In the end, regardless of the weather – it’s the timeless mood of the day that Claire strives to capture.</p>
    </section>
  </div>

  <blockquote class="testimonial">
    <p class="testimonial__quote">“Words can’t express my thanks Claire, I am absolutely in awe of my photos! You’ve captured my wedding day perfectly; couldn’t ask for anything more.”</p>
    <cite class="testimonial__cite">- Kate, Yarraville</cite>
  </blockquote>

  <p class="studio-name">Claire Ashdown</p>
</main>
</body>
</html>
```